We need a complete design for our construction company KELTO CONSTRUCTION based in Auckland New Zealand, we need a logo, website, business card, vehicle design etc..
We are a mid to high-end construction company who work mostly on residential projects and some commercial.

What we want to see in the design;
Professional,
Architectural,
Simple,
Alternative,

We want the design to communicate professionalism, high quality wormanship and and quality service.

Target Market(s)

People looking for a quality building/ construction company

Industry/Entity Type

Construction Company

Contact Information for Business Card

KELTO CONSTRUCTION.co.nz
Lino Verasek
lino@keltoconstruction.example.nz
021 5807 462

Logo Text

KELTO CONSTRUCTION

Number of Pages Required

5+ page

Font styles to use
Sans Serif

Colors

Designer to choose colors to be used in the design.

Requirements
Must have
• Must appear high end, professional, quality, be simple, easy to use, give security to potential clients
Nice to have
• high-quality photos of our recent projects
• about us page
• blog page
• contact us page
• high quality content
Should not have
• should not be hard to use and have too much going on.

```html
<!DOCTYPE html>
<html lang="en">
<head>
<meta charset="utf-8">
<title>Kelto Construction</title>
<link rel="stylesheet" href="https://fonts.googleapis.com/css2?family=Open+Sans:wght@400;600;700&family=Oswald:wght@400;600&display=swap">
<style>
:root{
  --blue:#1c5a9c;
  --blue-dark:#123f70;
  --slate:#34495e;
  --ink:#2b2b2b;
  --muted:#666;
  --grey-bg:#efefef;
  --footer:#2c2c2c;
  --white:#fff;
}
*{box-sizing:border-box;margin:0;padding:0}
html,body{width:1200px;height:3252px;overflow:hidden}
body{font-family:"Open Sans",Arial,sans-serif;color:var(--ink);background:var(--white)}
section,header,footer{overflow:hidden}
.photo{display:block}
/* header */
.site-header{height:120px;display:flex;align-items:center;justify-content:space-between;padding:0 60px 0 100px}
.brand{display:flex;align-items:center;gap:12px;white-space:nowrap}
.brand-mark{width:34px;height:34px;background:var(--blue);flex:none}
.brand-name{font-weight:700;font-size:20px;color:var(--blue);letter-spacing:.5px}
.header-right{display:flex;flex-direction:column;align-items:flex-end;gap:14px}
.contact-strip{display:flex;align-items:center;gap:22px;font-size:13px;color:var(--muted)}
.contact-strip .item{display:flex;align-items:center;gap:8px}
.dot-ic{width:26px;height:26px;border-radius:50%;background:var(--blue);display:inline-block}
.social{display:flex;gap:6px}
.social span{width:24px;height:24px;border-radius:50%;background:var(--blue);display:inline-block}
.main-nav{display:flex;gap:26px;font-size:14px;font-weight:600;color:var(--muted)}
.main-nav .active{color:var(--blue);border-bottom:3px solid var(--blue);padding-bottom:4px}
/* hero */
.hero{position:relative;height:520px;background:linear-gradient(100deg,#6d5a40 0%,#a8906a 45%,#d7d2c6 75%,#e9e6de 100%)}
.hero-title{position:absolute;left:220px;top:140px;font-family:"Oswald",sans-serif;font-size:52px;color:var(--white);background:rgba(60,45,30,.55);padding:6px 22px}
.hero-title b{font-weight:600;color:#f0c75a}
.hero-arrow{position:absolute;top:230px;width:34px;height:34px;background:rgba(0,0,0,.45)}
.hero-arrow.left{left:0}.hero-arrow.right{right:0}
/* project boxes */
.projects{display:flex;height:132px}
.project{flex:1;display:flex;align-items:center;gap:26px;padding:0 40px 0 100px;color:var(--white)}
.project.residential{background:var(--slate)}
.project.commercial{background:var(--blue);padding-left:40px}
.project .ic{width:80px;height:80px;border-radius:50%;background:rgba(255,255,255,.2);flex:none;display:flex;align-items:center;justify-content:center}
.project h3{font-size:20px;font-weight:700;margin-bottom:6px}
.project p{font-size:13px;line-height:1.5;opacity:.9;max-width:300px}
/* section heads */
.section-title{text-align:center;font-size:30px;font-weight:700;color:var(--slate);letter-spacing:1px;line-height:36px}
.section-title span{color:var(--blue)}
.title-mark{display:block;margin:8px auto 0;width:26px;height:20px}
.btn{display:block;margin:0 auto;width:120px;height:36px;line-height:36px;text-align:center;background:#666;color:var(--white);font-size:13px;font-weight:700}
/* about */
.about{height:388px;padding-top:46px}
.about p{width:1040px;margin:26px auto 28px;font-size:14px;line-height:1.9;color:var(--muted);text-align:center}
/* specializing */
.specialize{background:var(--grey-bg);height:560px;padding-top:44px}
.cards{display:flex;justify-content:center;gap:26px;margin-top:28px}
.card{width:292px;background:var(--white);box-shadow:0 2px 6px rgba(0,0,0,.12);text-align:center;padding-bottom:20px}
.card .photo{height:170px}
.card .badge{width:60px;height:60px;border-radius:50%;background:var(--blue);margin:-30px auto 12px;position:relative;border:4px solid var(--white)}
.card h4{font-size:17px;font-weight:700;color:var(--slate);margin-bottom:8px}
.card p{font-size:13px;line-height:1.6;color:var(--muted);padding:0 20px;margin-bottom:14px}
/* work */
.work{height:680px;padding-top:50px}
.work-grid{position:relative;width:1000px;height:380px;margin:40px auto 48px}
.tile{position:absolute}
.tile .label{position:absolute;left:50%;top:50%;transform:translate(-50%,-50%);color:var(--white);font-size:12px;font-weight:700;background:rgba(0,0,0,.45);padding:4px 10px;white-space:nowrap}
.view-btn{width:100px;height:34px;line-height:34px}
/* blog */
.blog{background:var(--grey-bg);height:516px;padding-top:40px}
.blog-wrap{display:flex;gap:26px;width:900px;margin:32px auto 28px}
.blog-feature{width:392px}
.blog-feature .photo{height:280px}
.meta{display:flex;gap:14px;font-size:12px;color:var(--blue);margin-top:6px}
.blog-list{flex:1;display:flex;flex-direction:column;gap:14px}
.post{display:flex;gap:16px}
.post .photo{width:112px;height:84px;flex:none}
.post h5{font-size:15px;font-weight:700;color:var(--slate)}
.post p{font-size:12px;color:var(--muted);line-height:1.5;margin-top:4px}
/* footer */
.site-footer{height:284px;background:var(--footer);color:#ccc;display:flex;padding:40px 100px 0;gap:60px}
.site-footer h6{color:var(--white);font-size:15px;font-weight:700;margin-bottom:18px;white-space:nowrap}
.quick{flex:none;width:110px}
.quick ul{list-style:none;font-size:13px;line-height:2}
.quick li::before{content:"›";margin-right:8px;color:var(--white)}
.contact-list div{font-size:13px;margin-bottom:14px;display:flex;gap:10px}
.contact-list i{width:14px;height:14px;border-radius:50%;background:var(--blue);display:inline-block;flex:none;margin-top:3px}
.map .photo{width:240px;height:160px}
.footer-brand{margin-left:auto;text-align:center;padding-top:40px}
.footer-brand .brand-name{color:var(--white);font-size:18px}
.footer-brand .social{justify-content:center;margin-top:14px}
.copyright{height:52px;line-height:52px;background:var(--blue-dark);color:#dde;text-align:center;font-size:12px}
</style>
</head>
<body>
<header class="site-header">
  <div class="brand"><span class="brand-mark"></span><span class="brand-name">KELTO CONSTRUCTION</span></div>
  <div class="header-right">
    <div class="contact-strip">
      <span class="item"><span class="dot-ic"></span>123-456-7890</span>
      <span class="item"><span class="dot-ic"></span>info@keltoconstruction.example.nz</span>
      <span class="social"><span></span><span></span><span></span><span></span></span>
    </div>
    <nav class="main-nav"><span class="active">HOME</span><span>ABOUT US</span><span>SERVICES</span><span>OUR WORK</span><span>BLOG</span><span>CONTACT US</span></nav>
  </div>
</header>

<section class="hero photo" role="img" aria-label="Hard hat and blueprints in front of a construction site with cranes">
  <span class="hero-arrow left"></span><span class="hero-arrow right"></span>
  <div class="hero-title">We Build <b>Your Dreams</b></div>
</section>

<section class="projects">
  <div class="project residential">
    <div class="ic"><svg width="40" height="36" viewBox="0 0 40 36"><path d="M4 18 20 4l16 14M9 15v17h22V15" fill="none" stroke="#fff" stroke-width="3"/></svg></div>
    <div><h3>RESIDENTIAL PROJECTS</h3><p>Lorem ipsum dolor sit amet, consectetur adipiscing elit, sed diam nonummy nibh euismod tincidunt [...]</p></div>
  </div>
  <div class="project commercial">
    <div class="ic"><svg width="34" height="40" viewBox="0 0 34 40"><rect x="5" y="3" width="24" height="35" fill="none" stroke="#fff" stroke-width="3"/><path d="M11 10h4M19 10h4M11 17h4M19 17h4M11 24h4M19 24h4" stroke="#fff" stroke-width="3"/></svg></div>
    <div><h3>COMMERCIAL PROJECTS</h3><p>Lorem ipsum dolor sit amet, consectetur adipiscing elit, sed diam nonummy nibh euismod tincidunt [...]</p></div>
  </div>
</section>

<section class="about">
  <h2 class="section-title">ABOUT <span>KELTO</span> CONSTRUCTION</h2>
  <svg class="title-mark" viewBox="0 0 26 20"><path d="M2 18 13 3l11 15z" fill="#1c5a9c"/></svg>
  <p>Lorem ipsum dolor sit amet, consectetuer adipiscing elit, sed diam nonummy nibh euismod tincidunt ut laoreet dolore magna aliquam erat volutpat. Ut wisi enim ad minim veniam, quis nostrud exerci tation ullamcorper suscipit lobortis nisl ut aliquip ex ea commodo consequat. Duis autem vel eum iriure dolor in hendrerit in vulputate velit esse molestie consequat, vel illum dolore eu feugiat nulla facilisis at vero eros et accumsan et iusto odio dignissim qui blandit praesent luptatum zzril delenit augue duis dolore te feugait nulla facilisi. Nam liber tempor cum soluta nobis eleifend option congue nihil imperdiet doming id quod mazim placerat.</p>
  <span class="btn">READ MORE</span>
</section>

<section class="specialize">
  <h2 class="section-title">WE <span>SPECIALIZING</span> IN</h2>
  <svg class="title-mark" viewBox="0 0 26 20"><path d="M2 18 13 3l11 15z" fill="#1c5a9c"/></svg>
  <div class="cards">
    <article class="card"><div class="photo" role="img" aria-label="Builders in hard hats reviewing interior renovation" style="background:linear-gradient(135deg,#c9b089,#e7dccb)"></div><div class="badge"></div><h4>INTERIOR RENOVATION</h4><p>Lorem ipsum dolor sit amet, consectetur adipiscing elit. Praesent vestibulum folia. Phasellus ac faucibus.</p><span class="btn">READ MORE</span></article>
    <article class="card"><div class="photo" role="img" aria-label="Client meeting over design and build plans" style="background:linear-gradient(135deg,#8fa3b8,#d8dfe6)"></div><div class="badge"></div><h4>DESIGN &amp; BUILD PACKAGE</h4><p>Lorem ipsum dolor sit amet, consectetur adipiscing elit. Praesent vestibulum folia. Phasellus ac faucibus.</p><span class="btn">READ MORE</span></article>
    <article class="card"><div class="photo" role="img" aria-label="Tradespeople tiling and painting" style="background:linear-gradient(135deg,#d9b14a,#eeeeee)"></div><div class="badge"></div><h4>TILING AND PAINTING</h4><p>Lorem ipsum dolor sit amet, consectetur adipiscing elit. Praesent vestibulum folia. Phasellus ac faucibus.</p><span class="btn">READ MORE</span></article>
  </div>
</section>

<section class="work">
  <h2 class="section-title">OUR <span>WORK</span></h2>
  <svg class="title-mark" viewBox="0 0 26 20"><path d="M2 18 13 3l11 15z" fill="#1c5a9c"/></svg>
  <div class="work-grid">
    <div class="tile photo" role="img" aria-label="Timber frame interior under construction" style="left:0;top:0;width:235px;height:185px;background:#6b5a48"><span class="label">LOREM IPSUM</span></div>
    <div class="tile photo" role="img" aria-label="Renovated living space" style="left:255px;top:0;width:235px;height:185px;background:#8a8a84"><span class="label">LOREM IPSUM</span></div>
    <div class="tile photo" role="img" aria-label="Modern glass office tower" style="left:510px;top:0;width:235px;height:380px;background:linear-gradient(#7f9bb8,#3d5670)"><span class="label">LOREM IPSUM</span></div>
    <div class="tile photo" role="img" aria-label="Plans and tools on a desk" style="left:765px;top:0;width:235px;height:185px;background:#d7c9a4"><span class="label">LOREM IPSUM</span></div>
    <div class="tile photo" role="img" aria-label="Finished two-storey family home" style="left:0;top:195px;width:490px;height:185px;background:linear-gradient(#9bb0c4,#7b8f6a)"><span class="label">LOREM IPSUM</span></div>
    <div class="tile photo" role="img" aria-label="Workers reviewing site drawings" style="left:765px;top:195px;width:235px;height:185px;background:#a07b5a"><span class="label">LOREM IPSUM</span></div>
  </div>
  <span class="btn view-btn">VIEW ALL</span>
</section>

<section class="blog">
  <h2 class="section-title">LATEST <span>BLOG POSTS</span></h2>
  <svg class="title-mark" viewBox="0 0 26 20"><path d="M2 18 13 3l11 15z" fill="#1c5a9c"/></svg>
  <div class="blog-wrap">
    <div class="blog-feature">
      <div class="photo" role="img" aria-label="High-rise building with crane under construction" style="background:linear-gradient(#6e9cc9,#2f5e8c)"></div>
      <div class="meta"><span>19Mar 2018</span><span>153 Comments</span><span>291 Likes</span></div>
    </div>
    <div class="blog-list">
      <div class="post"><div class="photo" role="img" aria-label="Construction workers on site" style="background:#8a7d6a"></div><div><h5>Lorem ipsum dolor sit amet consectetur.</h5><div class="meta"><span>19Mar 2018</span><span>153 Comments</span><span>291 Likes</span></div><p>Lorem ipsum dolor sit amet consectetur adipiscing elit sed diam nonummy nibh euismod tincidunt [...]</p></div></div>
      <div class="post"><div class="photo" role="img" aria-label="Crane against a blue sky" style="background:#7fa0bf"></div><div><h5>Lorem ipsum dolor sit amet consectetur.</h5><div class="meta"><span>19Mar 2018</span><span>153 Comments</span><span>291 Likes</span></div><p>Lorem ipsum dolor sit amet consectetur adipiscing elit sed diam nonummy nibh euismod tincidunt [...]</p></div></div>
      <div class="post"><div class="photo" role="img" aria-label="Building frame at dusk" style="background:#9a8a78"></div><div><h5>Lorem ipsum dolor sit amet consectetur.</h5><div class="meta"><span>19Mar 2018</span><span>153 Comments</span><span>291 Likes</span></div><p>Lorem ipsum dolor sit amet consectetur adipiscing elit sed diam nonummy nibh euismod tincidunt [...]</p></div></div>
    </div>
  </div>
  <span class="btn view-btn">VIEW ALL</span>
</section>

<footer class="site-footer">
  <div class="quick"><h6>QUICK LINKS</h6><ul><li>Home</li><li>About Us</li><li>Services</li><li>Our Work</li><li>Blog</li><li>Contact Us</li></ul></div>
  <div class="contact-list"><h6>CONTACT DETAILS</h6>
    <div><i></i><span>KELTO CONSTRUCTION<br>1233 www ipsum dolor sit amet,<br>consectetuer adipiscing elit</span></div>
    <div><i></i><span>123-456-7890</span></div>
    <div><i></i><span>123-456-7890</span></div>
    <div><i></i><span>info@keltoconstruction.example.nz</span></div>
  </div>
  <div class="map"><h6>LOCATION MAP</h6><div class="photo" role="img" aria-label="Street map of the office location" style="background:#d9dcd6"></div></div>
  <div class="footer-brand"><div class="brand"><span class="brand-mark"></span><span class="brand-name">KELTO CONSTRUCTION</span></div><div class="social"><span></span><span></span><span></span><span></span></div></div>
</footer>
<div class="copyright">Copyright © 2018 KELTO CONSTRUCTION. All Rights Reserved.</div>
</body>
</html>
```